International online gaming platform needs a game UI design

1. We need a game interface for three kinds of theme based on our guideline and sample mockup.
2. The product type is the online casino games related, we need a series of casino games UIs, however, we can start on the game lobby first.
3. Three theme you might choose from or refer to:
A. 3D look & feel
B. Realistic casino theme
C. Richness and grandeur
D. European casino style
4. NOT ALLOWED to change the design layout.
MUST follow our sample mock up and ONLY redefine the design style.
5. All items must be in a stand-alone component, eg. Button, Tab, Icon,... etc.
6. We need the layout in vector shape, but we can review in JPG or PNG format.
7. The image size: 1366 x 768

Updated:
1. All items and their positions should be same as the sample UI we provided.
Please redesign all the items and create a new theme for it.
No need to create a new layout.
2. Although we accept the draft design, but all the items in UI should be completed.
3. All the wordings in the sample UI are confirmed, you might change the fonts.
4. For the avatar in the left hand side, you don't have to redraw it.
We already have our own avatar system implemented.
5. All the items such as icons, tabs, and buttons are free to redesign.

Dear designers,

We've increased our budget and raise the prize money to 800 USD.  
We also accept the draft design in PNG format and we can go through the details in handover stage.
Thank you very much. 

Reason: Dear designers, We decided to extend the deadline by 7 days. As mentioned in the task description, we are looking for a new style of design and you might refer to the below style. A. 3D look & feel B. Realistic casino theme C. Richness and grandeur D. European casino style If you are still interested in our project, please send us your work. Thank you very much!

```html
<!DOCTYPE html>
<html lang="en">
<head>
<meta charset="utf-8">
<title>Live Casino Lobby</title>
<link rel="stylesheet" href="https://fonts.googleapis.com/css2?family=Open+Sans:wght@400;600;700&family=Titillium+Web:wght@600;700;900&display=swap">
<style>
  :root {
    --bg-deep: #120404;
    --bg-dark: #240606;
    --red-dark: #4a0a0a;
    --red: #8d1414;
    --red-bright: #c4201c;
    --red-glow: #e2382a;
    --orange: #f08a1c;
    --gold: #f7c531;
    --gold-pale: #ffe58a;
    --cream: #fff6cf;
    --white: #ffffff;
    --grey: #d8d8d8;
    --text-dim: #e8d6c8;
  }
  * { box-sizing: border-box; margin: 0; padding: 0; }
  html, body { width: 1200px; height: 675px; overflow: hidden; background: var(--bg-deep); }
  body { font-family: "Open Sans", Arial, sans-serif; color: var(--white); }
  .lobby {
    position: relative; width: 1200px; height: 675px; overflow: hidden;
    background: linear-gradient(180deg, #2b0707 0%, #1a0404 40%, #2b0808 100%);
  }
  .abs { position: absolute; }

  /* Header */
  .header { left: 0; top: 0; width: 1200px; height: 40px;
    background: linear-gradient(180deg, #5a0d0d, #2a0505); border-bottom: 2px solid var(--red-bright); }
  .brand { left: 0; top: 0; width: 380px; height: 40px;
    background: linear-gradient(90deg, #7a1010, #3c0808 85%, transparent);
    clip-path: polygon(0 0, 100% 0, 92% 100%, 0 100%);
    display: flex; align-items: center; gap: 10px; padding-left: 10px; }
  .brand-dot { width: 22px; height: 22px; border-radius: 50%; background: var(--gold); }
  .brand-name { font-family: "Titillium Web", sans-serif; font-weight: 900; font-size: 30px;
    letter-spacing: 1px; color: var(--gold); line-height: 1; }
  .tools { right: 12px; top: 5px; display: flex; gap: 6px; }
  .tool { width: 28px; height: 28px; border: 1px solid var(--gold);
    background: linear-gradient(180deg, #ff9a2a, #c4400c); display: grid; place-items: center; }

  /* Left column */
  .clock { left: 12px; top: 52px; width: 164px; height: 26px; border: 1px solid var(--gold);
    border-radius: 4px; background: #2a0707; font-size: 10px; color: var(--gold-pale);
    display: grid; place-items: center; }
  .side { left: 12px; top: 90px; width: 162px; height: 530px; border: 2px solid var(--orange);
    border-radius: 6px; background: linear-gradient(180deg, #2b0606, #7a1212 60%, #2b0606); }
  .player { left: 18px; top: 96px; width: 150px; height: 258px; border: 2px solid #b0406a;
    border-radius: 4px; background: linear-gradient(180deg, #8d1414, #3a0808); }
  .avatar { left: 24px; top: 100px; width: 138px; height: 162px; background: #ececec; border: 2px solid #a0303a; }
  .username { left: 24px; top: 268px; width: 138px; text-align: center; font-size: 10px;
    font-weight: 700; color: var(--gold); letter-spacing: .5px; }
  .side-btn { left: 22px; width: 142px; height: 34px; border: 1px solid var(--gold); border-radius: 4px;
    background: linear-gradient(180deg, #8d1414, #3a0707); display: flex; align-items: center; gap: 8px;
    padding-left: 6px; font-size: 11px; color: var(--white); }
  .side-btn.profile { left: 24px; top: 312px; width: 138px; height: 26px;
    background: linear-gradient(180deg, #c27a3a, #6a2a10); }
  .ico { width: 22px; height: 22px; background: linear-gradient(180deg, #6a1a0a, #2a0505);
    border: 1px solid var(--orange); display: grid; place-items: center; flex: none; }

  /* Main frame */
  .main { left: 186px; top: 40px; width: 1014px; height: 596px; border-left: 2px solid var(--red-bright);
    background: linear-gradient(180deg, #8a1212, #3a0707 50%, #2a0505); }

  /* Tabs */
  .tab { top: 54px; width: 229px; height: 34px; border: 2px solid #5a2a10; border-radius: 6px 6px 0 0;
    background: linear-gradient(180deg, #8a5a2a, #3a1a08); display: flex; align-items: center;
    padding-left: 76px; font-family: "Titillium Web", sans-serif; font-weight: 700; font-size: 20px; color: var(--white); }
  .tab.active { border-color: var(--orange); background: linear-gradient(180deg, #b02418, #4a0a08); }
  .tab-art { position: absolute; left: 8px; top: -10px; width: 56px; height: 44px; border-radius: 8px; }

  /* Dealers */
  .hero { left: 200px; top: 96px; width: 286px; height: 132px; border: 2px solid var(--orange);
    border-radius: 6px; background: linear-gradient(180deg, #c42a18, #6a1010); }
  .dealer-photo { background: linear-gradient(180deg, #3f7fcf, #12408a); border: 2px solid var(--gold); }
  .road { background-color: #fffbe2;
    background-image: linear-gradient(#e6d98a 1px, transparent 1px), linear-gradient(90deg, #e6d98a 1px, transparent 1px);
    background-size: 12px 12px; }
  .road.grey { background-color: #ffffff;
    background-image: linear-gradient(45deg, #dcdcdc 25%, transparent 25%, transparent 75%, #dcdcdc 75%),
                      linear-gradient(45deg, #dcdcdc 25%, transparent 25%, transparent 75%, #dcdcdc 75%);
    background-size: 14px 14px; background-position: 0 0, 7px 7px; }
  .beads { position: absolute; left: 2px; top: 2px; display: flex; gap: 2px; }
  .bead { width: 9px; height: 9px; border-radius: 50%; border: 2px solid var(--red-bright); background: #fff; }
  .bead.g { border-color: #1a9a3a; }
  .nameplate { background: #1a0303; border: 1px solid #aaa; display: flex; justify-content: space-between;
    align-items: center; color: var(--white); }
  .nameplate b { background: var(--red-bright); font-weight: 400; height: 100%; display: flex; align-items: center; padding: 0 6px; }
  .deck { left: 498px; top: 102px; width: 678px; height: 116px; border: 3px solid var(--orange);
    border-radius: 10px; background: linear-gradient(180deg, #3a0a08, #1a0303); }

  /* Filter bar */
  .multi { left: 212px; top: 240px; width: 144px; height: 32px; border: 1px solid #c07a3a; border-radius: 4px;
    background: linear-gradient(180deg, #a06a3a, #5a2a10); display: flex; align-items: center; gap: 8px;
    padding-left: 4px; font-size: 11px; font-weight: 700; }
  .search { left: 358px; top: 240px; width: 290px; height: 32px; border-radius: 4px;
    background: linear-gradient(180deg, #5a1a0a, #2a0505); border: 1px solid #6a2a10; }
  .filters { left: 657px; top: 238px; width: 518px; height: 36px; border-radius: 6px;
    background: linear-gradient(180deg, #a02016, #4a0808); display: flex; gap: 2px; padding: 4px 5px; }
  .chip { height: 28px; background: linear-gradient(180deg, #e0a050, #8a4a10); border-radius: 2px;
    display: grid; place-items: center; font-size: 14px; color: var(--white); }

  /* Table cards */
  .card { width: 310px; height: 155px; border: 2px solid #c42a18; border-radius: 10px;
    background: linear-gradient(180deg, #7a1010, #3a0707 45%, #8a1414); overflow: hidden; }
  .card-title { position: absolute; left: 12px; top: 6px; font-family: "Titillium Web", sans-serif;
    font-weight: 700; font-size: 11px; color: var(--gold); }
  .card-comm { position: absolute; right: 12px; top: 6px; font-family: "Titillium Web", sans-serif;
    font-weight: 700; font-size: 11px; color: var(--gold); }
  .card-limit { position: absolute; left: 12px; top: 23px; font-size: 11px; color: var(--text-dim); }
  .card-count { position: absolute; right: 12px; top: 23px; font-size: 11px; color: var(--text-dim); }
  .join { position: absolute; left: 100px; top: 18px; width: 106px; height: 32px; border-radius: 16px;
    border: 3px solid var(--gold); background: radial-gradient(#e8301c, #a01010);
    display: grid; place-items: center; font-family: "Titillium Web", sans-serif; font-weight: 700;
    font-size: 18px; color: var(--white); }
  .board { position: absolute; left: 0; top: 60px; }
  .seats { position: absolute; left: 4px; top: 118px; display: flex; gap: 5px; }
  .seat { width: 38px; height: 26px; border-radius: 2px; background: linear-gradient(180deg, #e03a1c, #a01a10);
    display: grid; place-items: center; }

  .scroll { left: 1168px; top: 284px; width: 12px; height: 334px; background: #0e0202; border: 1px solid #3a0808; }
  .thumb { left: 1170px; top: 284px; width: 8px; height: 18px; background: var(--cream); }

  /* Footer */
  .footer { left: 0; top: 636px; width: 1200px; height: 39px; background: linear-gradient(180deg, #3a0707, #1a0303);
    border-top: 2px solid var(--red-bright); }
  .balance { left: 928px; top: 640px; width: 268px; height: 30px; border: 1px solid var(--gold); border-radius: 4px;
    background: linear-gradient(90deg, #a01a10, #1a0303 35%); display: flex; align-items: center; padding-left: 8px;
    font-size: 16px; }
  .currency { margin-left: 8px; width: 46px; height: 22px; border: 1px solid var(--gold); background: #3a2a05;
    font-size: 12px; color: var(--gold); display: grid; place-items: center; }
  .amount { margin-left: auto; margin-right: 24px; font-size: 15px; }
</style>
</head>
<body>
<main class="lobby">
  <header class="abs header">
    <div class="abs brand"><span class="brand-dot"></span><span class="brand-name">LIVE CASINO</span></div>
    <div class="abs tools">
      <span class="tool"><svg width="16" height="16" viewBox="0 0 16 16"><circle cx="7" cy="7" r="5" fill="none" stroke="#3a0a05" stroke-width="2"/><path d="M5 7h4M7 5v4M11 11l4 4" stroke="#3a0a05" stroke-width="2"/></svg></span>
      <span class="tool"><svg width="16" height="16" viewBox="0 0 16 16"><circle cx="7" cy="7" r="5" fill="none" stroke="#3a0a05" stroke-width="2"/><path d="M5 7h4M11 11l4 4" stroke="#3a0a05" stroke-width="2"/></svg></span>
      <span class="tool"><svg width="16" height="16" viewBox="0 0 16 16"><path d="M5 12V3l8-2v9" fill="none" stroke="#3a0a05" stroke-width="2"/><circle cx="4" cy="12" r="2.5" fill="#3a0a05"/><circle cx="12" cy="10" r="2.5" fill="#3a0a05"/></svg></span>
      <span class="tool"><svg width="16" height="16" viewBox="0 0 16 16"><path d="M1 5V1h4M11 1h4v4M15 11v4h-4M5 15H1v-4M2 2l4 4M14 2l-4 4M14 14l-4-4M2 14l4-4" fill="none" stroke="#3a0a05" stroke-width="2"/></svg></span>
      <span class="tool"><svg width="16" height="16" viewBox="0 0 16 16"><path d="M3 3l10 10M13 3L3 13" stroke="#3a0a05" stroke-width="2.5"/></svg></span>
    </div>
  </header>

  <div class="abs clock">1/28/2014 06:54 PM GMT+8</div>
  <aside class="abs side"></aside>
  <div class="abs player"></div>
  <div class="abs avatar" role="img" aria-label="Player avatar"></div>
  <div class="abs username">ALPos848767</div>
  <div class="abs side-btn profile"><span class="ico"><svg width="12" height="12" viewBox="0 0 12 12"><rect x="1" y="1" width="10" height="10" fill="none" stroke="#f7c531"/><path d="M3 4h6M3 6h6M3 8h6" stroke="#f7c531"/></svg></span>Profile</div>
  <div class="abs side-btn" style="top:364px"><span class="ico"><svg width="12" height="12" viewBox="0 0 12 12"><path d="M2 4h2l4-3v10L4 8H2z" fill="#f7c531"/></svg></span>Announcements</div>
  <div class="abs side-btn" style="top:406px"><span class="ico"><svg width="12" height="12" viewBox="0 0 12 12"><rect x="1" y="1" width="10" height="10" fill="none" stroke="#f7c531"/><path d="M4 1v10" stroke="#f7c531"/></svg></span>Rules &amp; Regulation</div>
  <div class="abs side-btn" style="top:448px"><span class="ico"><svg width="12" height="12" viewBox="0 0 12 12"><circle cx="5" cy="5" r="3.5" fill="none" stroke="#f7c531" stroke-width="1.5"/><path d="M7.5 7.5L11 11" stroke="#f7c531" stroke-width="1.5"/></svg></span>Quick tour</div>

  <section class="abs main"></section>

  <nav>
    <div class="abs tab active" style="left:196px"><span class="tab-art" style="background:linear-gradient(135deg,#f2f2f2,#9a9a9a)" role="img" aria-label="Playing cards"></span>Bacarat</div>
    <div class="abs tab" style="left:436px"><span class="tab-art" style="background:linear-gradient(135deg,#5aa0e0,#1a3a7a)" role="img" aria-label="Casino chip"></span>Super six</div>
    <div class="abs tab" style="left:676px"><span class="tab-art" style="background:radial-gradient(#d0a070,#5a2a10)" role="img" aria-label="Roulette wheel"></span>Roulette</div>
    <div class="abs tab" style="left:918px"><span class="tab-art" style="background:radial-gradient(#e04040,#5a5a5a)" role="img" aria-label="Dice under a dome"></span>Sic Bo</div>
  </nav>

  <section class="abs hero">
    <div class="abs dealer-photo" style="left:16px;top:8px;width:84px;height:86px" role="img" aria-label="Dealer photo"></div>
    <div class="abs road" style="left:102px;top:8px;width:172px;height:86px"><div class="beads"><i class="bead g"></i><i class="bead"></i><i class="bead"></i><i class="bead g"></i><i class="bead"></i></div></div>
    <div class="abs nameplate" style="left:14px;top:98px;width:260px;height:22px;font-size:12px;padding-left:6px">Dealer Name<b>Deals 999</b></div>
  </section>

  <section class="abs deck">
    <div class="abs dealer-photo" style="left:14px;top:14px;width:70px;height:70px;border-color:#7a1010;background:linear-gradient(180deg,#c43a2a,#5a0a0a)" role="img" aria-label="Dealer photo"></div>
    <div class="abs road grey" style="left:84px;top:14px;width:136px;height:70px"><div class="beads"><i class="bead g"></i><i class="bead"></i><i class="bead"></i><i class="bead g"></i><i class="bead"></i></div></div>
    <div class="abs nameplate" style="left:14px;top:86px;width:206px;height:18px;font-size:10px;padding-left:5px">Dealer Name<b>Deals 999</b></div>
    <div class="abs dealer-photo" style="left:234px;top:14px;width:70px;height:70px;border-color:#7a1010;background:linear-gradient(180deg,#c43a2a,#5a0a0a)" role="img" aria-label="Dealer photo"></div>
    <div class="abs road grey" style="left:304px;top:14px;width:136px;height:70px"><div class="beads"><i class="bead g"></i><i class="bead"></i><i class="bead"></i><i class="bead g"></i><i class="bead"></i></div></div>
    <div class="abs nameplate" style="left:234px;top:86px;width:206px;height:18px;font-size:10px;padding-left:5px">Dealer Name<b>Deals 999</b></div>
    <div class="abs dealer-photo" style="left:454px;top:14px;width:70px;height:70px;border-color:#7a1010;background:linear-gradient(180deg,#c43a2a,#5a0a0a)" role="img" aria-label="Dealer photo"></div>
    <div class="abs road grey" style="left:524px;top:14px;width:136px;height:70px"><div class="beads"><i class="bead g"></i><i class="bead"></i><i class="bead"></i><i class="bead g"></i></div></div>
    <div class="abs nameplate" style="left:454px;top:86px;width:206px;height:18px;font-size:10px;padding-left:5px">Dealer Name<b>Deals 999</b></div>
  </section>

  <div class="abs multi"><span class="ico" style="border-color:#f7c531"><svg width="14" height="14" viewBox="0 0 14 14"><circle cx="5" cy="4" r="2.5" fill="#f7c531"/><path d="M1 12c0-3 2-4.5 4-4.5s4 1.5 4 4.5z" fill="#f7c531"/><circle cx="10" cy="5" r="2" fill="#f7c531"/><path d="M9 12c0-2 1-3.5 3.5-3.5V12z" fill="#f7c531"/></svg></span>Multiplayer</div>
  <div class="abs search"></div>
  <div class="abs filters">
    <span class="chip" style="width:112px">Join any</span>
    <span class="chip" style="width:44px;font-size:12px">A•Z</span>
    <span class="chip" style="width:44px">$⬇</span>
    <span class="chip" style="width:44px">$⬆</span>
    <span class="chip" style="width:44px"><svg width="22" height="12" viewBox="0 0 22 12"><g fill="#fff"><circle cx="4" cy="3" r="2"/><circle cx="11" cy="3" r="2"/><circle cx="18" cy="3" r="2"/><rect x="1" y="6" width="6" height="5"/><rect x="8" y="6" width="6" height="5"/><rect x="15" y="6" width="6" height="5"/></g></svg></span>
    <span class="chip" style="width:44px">&lt;3</span>
    <span class="chip" style="width:44px">&gt;3</span>
    <span class="chip" style="width:110px">All Limits ▾</span>
  </div>

  <section class="tables">
    <article class="abs card" style="left:204px;top:286px">
      <span class="card-title">Baccarat A5-3C</span><span class="card-comm">Commission 0/7</span>
      <span class="card-limit">Bet Limit</span><span class="card-count">0/100</span>
      <span class="join">JOIN</span>
      <svg class="board" width="310" height="54" viewBox="0 0 310 54"><g fill="none" stroke="#fff" stroke-width="1"><polygon points="22,2 288,2 304,52 6,52"/><line x1="19" y1="12" x2="291" y2="12"/><line x1="13" y1="30" x2="297" y2="30"/><line x1="60" y1="2" x2="48.6" y2="52"/><line x1="98" y1="2" x2="91.1" y2="52"/><line x1="136" y1="2" x2="133.7" y2="52"/><line x1="174" y1="2" x2="176.3" y2="52"/><line x1="212" y1="2" x2="218.9" y2="52"/><line x1="250" y1="2" x2="261.4" y2="52"/></g><g fill="#fff" font-family="Open Sans, sans-serif" font-style="italic" font-weight="700" font-size="12" text-anchor="middle"><text x="35" y="26">B</text><text x="75" y="26">B</text><text x="115" y="26">B</text><text x="155" y="26">B</text><text x="195" y="26">B</text><text x="235" y="26">B</text><text x="275" y="26">B</text><text x="30" y="46">P</text><text x="72" y="46">P</text><text x="114" y="46">P</text><text x="155" y="46">P</text><text x="197" y="46">P</text><text x="239" y="46">P</text><text x="280" y="46">P</text></g></svg>
      <div class="seats"><span class="seat"><svg width="16" height="16" viewBox="0 0 16 16"><circle cx="8" cy="5" r="4" fill="#ffc23a"/><path d="M1 16c0-5 3-7 7-7s7 2 7 7z" fill="#ffc23a"/></svg></span><span class="seat"><svg width="16" height="16" viewBox="0 0 16 16"><circle cx="8" cy="5" r="4" fill="#ffc23a"/><path d="M1 16c0-5 3-7 7-7s7 2 7 7z" fill="#ffc23a"/></svg></span><span class="seat"><svg width="16" height="16" viewBox="0 0 16 16"><circle cx="8" cy="5" r="4" fill="#ffc23a"/><path d="M1 16c0-5 3-7 7-7s7 2 7 7z" fill="#ffc23a"/></svg></span><span class="seat"><svg width="16" height="16" viewBox="0 0 16 16"><circle cx="8" cy="5" r="4" fill="#ffc23a"/><path d="M1 16c0-5 3-7 7-7s7 2 7 7z" fill="#ffc23a"/></svg></span><span class="seat"><svg width="16" height="16" viewBox="0 0 16 16"><circle cx="8" cy="5" r="4" fill="#ffc23a"/><path d="M1 16c0-5 3-7 7-7s7 2 7 7z" fill="#ffc23a"/></svg></span><span class="seat"><svg width="16" height="14" viewBox="0 0 16 14"><path d="M4 0h8v6h4l-8 8-8-8h4z" fill="#7a0a08"/></svg></span><span class="seat"><svg width="16" height="14" viewBox="0 0 16 14"><path d="M4 0h8v6h4l-8 8-8-8h4z" fill="#7a0a08"/></svg></span></div>
    </article>

    <article class="abs card" style="left:526px;top:286px">
      <span class="card-title">Baccarat A5-3C</span><span class="card-comm">Commission 0/7</span>
      <span class="card-limit">Bet Limit</span><span class="card-count">0/100</span>
      <span class="join">JOIN</span>
      <svg class="board" width="310" height="54" viewBox="0 0 310 54"><g fill="none" stroke="#fff" stroke-width="1"><polygon points="22,2 288,2 304,52 6,52"/><line x1="19" y1="12" x2="291" y2="12"/><line x1="13" y1="30" x2="297" y2="30"/><line x1="60" y1="2" x2="48.6" y2="52"/><line x1="98" y1="2" x2="91.1" y2="52"/><line x1="136" y1="2" x2="133.7" y2="52"/><line x1="174" y1="2" x2="176.3" y2="52"/><line x1="212" y1="2" x2="218.9" y2="52"/><line x1="250" y1="2" x2="261.4" y2="52"/></g><g fill="#fff" font-family="Open Sans, sans-serif" font-style="italic" font-weight="700" font-size="12" text-anchor="middle"><text x="35" y="26">B</text><text x="75" y="26">B</text><text x="115" y="26">B</text><text x="155" y="26">B</text><text x="195" y="26">B</text><text x="235" y="26">B</text><text x="275" y="26">B</text><text x="30" y="46">P</text><text x="72" y="46">P</text><text x="114" y="46">P</text><text x="155" y="46">P</text><text x="197" y="46">P</text><text x="239" y="46">P</text><text x="280" y="46">P</text></g></svg>
      <div class="seats"><span class="seat"><svg width="16" height="16" viewBox="0 0 16 16"><circle cx="8" cy="5" r="4" fill="#ffc23a"/><path d="M1 16c0-5 3-7 7-7s7 2 7 7z" fill="#ffc23a"/></svg></span><span class="seat"><svg width="16" height="16" viewBox="0 0 16 16"><circle cx="8" cy="5" r="4" fill="#ffc23a"/><path d="M1 16c0-5 3-7 7-7s7 2 7 7z" fill="#ffc23a"/></svg></span><span class="seat"><svg width="16" height="16" viewBox="0 0 16 16"><circle cx="8" cy="5" r="4" fill="#ffc23a"/><path d="M1 16c0-5 3-7 7-7s7 2 7 7z" fill="#ffc23a"/></svg></span><span class="seat"><svg width="16" height="16" viewBox="0 0 16 16"><circle cx="8" cy="5" r="4" fill="#ffc23a"/><path d="M1 16c0-5 3-7 7-7s7 2 7 7z" fill="#ffc23a"/></svg></span><span class="seat"><svg width="16" height="16" viewBox="0 0 16 16"><circle cx="8" cy="5" r="4" fill="#ffc23a"/><path d="M1 16c0-5 3-7 7-7s7 2 7 7z" fill="#ffc23a"/></svg></span><span class="seat"><svg width="16" height="14" viewBox="0 0 16 14"><path d="M4 0h8v6h4l-8 8-8-8h4z" fill="#7a0a08"/></svg></span><span class="seat"><svg width="16" height="14" viewBox="0 0 16 14"><path d="M4 0h8v6h4l-8 8-8-8h4z" fill="#7a0a08"/></svg></span></div>
    </article>

    <article class="abs card" style="left:848px;top:286px">
      <span class="card-title">Baccarat A5-3C</span><span class="card-comm">Commission 0/7</span>
      <span class="card-limit">Bet Limit</span><span class="card-count">0/100</span>
      <span class="join">JOIN</span>
      <svg class="board" width="310" height="54" viewBox="0 0 310 54"><g fill="none" stroke="#fff" stroke-width="1"><polygon points="22,2 288,2 304,52 6,52"/><line x1="19" y1="12" x2="291" y2="12"/><line x1="13" y1="30" x2="297" y2="30"/><line x1="60" y1="2" x2="48.6" y2="52"/><line x1="98" y1="2" x2="91.1" y2="52"/><line x1="136" y1="2" x2="133.7" y2="52"/><line x1="174" y1="2" x2="176.3" y2="52"/><line x1="212" y1="2" x2="218.9" y2="52"/><line x1="250" y1="2" x2="261.4" y2="52"/></g><g fill="#fff" font-family="Open Sans, sans-serif" font-style="italic" font-weight="700" font-size="12" text-anchor="middle"><text x="35" y="26">B</text><text x="75" y="26">B</text><text x="115" y="26">B</text><text x="155" y="26">B</text><text x="195" y="26">B</text><text x="235" y="26">B</text><text x="275" y="26">B</text><text x="30" y="46">P</text><text x="72" y="46">P</text><text x="114" y="46">P</text><text x="155" y="46">P</text><text x="197" y="46">P</text><text x="239" y="46">P</text><text x="280" y="46">P</text></g></svg>
      <div class="seats"><span class="seat"><svg width="16" height="16" viewBox="0 0 16 16"><circle cx="8" cy="5" r="4" fill="#ffc23a"/><path d="M1 16c0-5 3-7 7-7s7 2 7 7z" fill="#ffc23a"/></svg></span><span class="seat"><svg width="16" height="16" viewBox="0 0 16 16"><circle cx="8" cy="5" r="4" fill="#ffc23a"/><path d="M1 16c0-5 3-7 7-7s7 2 7 7z" fill="#ffc23a"/></svg></span><span class="seat"><svg width="16" height="16" viewBox="0 0 16 16"><circle cx="8" cy="5" r="4" fill="#ffc23a"/><path d="M1 16c0-5 3-7 7-7s7 2 7 7z" fill="#ffc23a"/></svg></span><span class="seat"><svg width="16" height="16" viewBox="0 0 16 16"><circle cx="8" cy="5" r="4" fill="#ffc23a"/><path d="M1 16c0-5 3-7 7-7s7 2 7 7z" fill="#ffc23a"/></svg></span><span class="seat"><svg width="16" height="16" viewBox="0 0 16 16"><circle cx="8" cy="5" r="4" fill="#ffc23a"/><path d="M1 16c0-5 3-7 7-7s7 2 7 7z" fill="#ffc23a"/></svg></span><span class="seat"><svg width="16" height="14" viewBox="0 0 16 14"><path d="M4 0h8v6h4l-8 8-8-8h4z" fill="#7a0a08"/></svg></span><span class="seat"><svg width="16" height="14" viewBox="0 0 16 14"><path d="M4 0h8v6h4l-8 8-8-8h4z" fill="#7a0a08"/></svg></span></div>
    </article>

    <article class="abs card" style="left:204px;top:458px">
      <span class="card-title">Baccarat A5-3C</span><span class="card-comm">Commission 0/7</span>
      <span class="card-limit">Bet Limit</span><span class="card-count">0/100</span>
      <span class="join">JOIN</span>
      <svg class="board" width="310" height="54" viewBox="0 0 310 54"><g fill="none" stroke="#fff" stroke-width="1"><polygon points="22,2 288,2 304,52 6,52"/><line x1="19" y1="12" x2="291" y2="12"/><line x1="13" y1="30" x2="297" y2="30"/><line x1="60" y1="2" x2="48.6" y2="52"/><line x1="98" y1="2" x2="91.1" y2="52"/><line x1="136" y1="2" x2="133.7" y2="52"/><line x1="174" y1="2" x2="176.3" y2="52"/><line x1="212" y1="2" x2="218.9" y2="52"/><line x1="250" y1="2" x2="261.4" y2="52"/></g><g fill="#fff" font-family="Open Sans, sans-serif" font-style="italic" font-weight="700" font-size="12" text-anchor="middle"><text x="35" y="26">B</text><text x="75" y="26">B</text><text x="115" y="26">B</text><text x="155" y="26">B</text><text x="195" y="26">B</text><text x="235" y="26">B</text><text x="275" y="26">B</text><text x="30" y="46">P</text><text x="72" y="46">P</text><text x="114" y="46">P</text><text x="155" y="46">P</text><text x="197" y="46">P</text><text x="239" y="46">P</text><text x="280" y="46">P</text></g></svg>
      <div class="seats"><span class="seat"><svg width="16" height="16" viewBox="0 0 16 16"><circle cx="8" cy="5" r="4" fill="#ffc23a"/><path d="M1 16c0-5 3-7 7-7s7 2 7 7z" fill="#ffc23a"/></svg></span><span class="seat"><svg width="16" height="16" viewBox="0 0 16 16"><circle cx="8" cy="5" r="4" fill="#ffc23a"/><path d="M1 16c0-5 3-7 7-7s7 2 7 7z" fill="#ffc23a"/></svg></span><span class="seat"><svg width="16" height="16" viewBox="0 0 16 16"><circle cx="8" cy="5" r="4" fill="#ffc23a"/><path d="M1 16c0-5 3-7 7-7s7 2 7 7z" fill="#ffc23a"/></svg></span><span class="seat"><svg width="16" height="16" viewBox="0 0 16 16"><circle cx="8" cy="5" r="4" fill="#ffc23a"/><path d="M1 16c0-5 3-7 7-7s7 2 7 7z" fill="#ffc23a"/></svg></span><span class="seat"><svg width="16" height="16" viewBox="0 0 16 16"><circle cx="8" cy="5" r="4" fill="#ffc23a"/><path d="M1 16c0-5 3-7 7-7s7 2 7 7z" fill="#ffc23a"/></svg></span><span class="seat"><svg width="16" height="14" viewBox="0 0 16 14"><path d="M4 0h8v6h4l-8 8-8-8h4z" fill="#7a0a08"/></svg></span><span class="seat"><svg width="16" height="14" viewBox="0 0 16 14"><path d="M4 0h8v6h4l-8 8-8-8h4z" fill="#7a0a08"/></svg></span></div>
    </article>

    <article class="abs card" style="left:526px;top:458px">
      <span class="card-title">Baccarat A5-3C</span><span class="card-comm">Commission 0/7</span>
      <span class="card-limit">Bet Limit</span><span class="card-count">0/100</span>
      <span class="join">JOIN</span>
      <svg class="board" width="310" height="54" viewBox="0 0 310 54"><g fill="none" stroke="#fff" stroke-width="1"><polygon points="22,2 288,2 304,52 6,52"/><line x1="19" y1="12" x2="291" y2="12"/><line x1="13" y1="30" x2="297" y2="30"/><line x1="60" y1="2" x2="48.6" y2="52"/><line x1="98" y1="2" x2="91.1" y2="52"/><line x1="136" y1="2" x2="133.7" y2="52"/><line x1="174" y1="2" x2="176.3" y2="52"/><line x1="212" y1="2" x2="218.9" y2="52"/><line x1="250" y1="2" x2="261.4" y2="52"/></g><g fill="#fff" font-family="Open Sans, sans-serif" font-style="italic" font-weight="700" font-size="12" text-anchor="middle"><text x="35" y="26">B</text><text x="75" y="26">B</text><text x="115" y="26">B</text><text x="155" y="26">B</text><text x="195" y="26">B</text><text x="235" y="26">B</text><text x="275" y="26">B</text><text x="30" y="46">P</text><text x="72" y="46">P</text><text x="114" y="46">P</text><text x="155" y="46">P</text><text x="197" y="46">P</text><text x="239" y="46">P</text><text x="280" y="46">P</text></g></svg>
      <div class="seats"><span class="seat"><svg width="16" height="16" viewBox="0 0 16 16"><circle cx="8" cy="5" r="4" fill="#ffc23a"/><path d="M1 16c0-5 3-7 7-7s7 2 7 7z" fill="#ffc23a"/></svg></span><span class="seat"><svg width="16" height="16" viewBox="0 0 16 16"><circle cx="8" cy="5" r="4" fill="#ffc23a"/><path d="M1 16c0-5 3-7 7-7s7 2 7 7z" fill="#ffc23a"/></svg></span><span class="seat"><svg width="16" height="16" viewBox="0 0 16 16"><circle cx="8" cy="5" r="4" fill="#ffc23a"/><path d="M1 16c0-5 3-7 7-7s7 2 7 7z" fill="#ffc23a"/></svg></span><span class="seat"><svg width="16" height="16" viewBox="0 0 16 16"><circle cx="8" cy="5" r="4" fill="#ffc23a"/><path d="M1 16c0-5 3-7 7-7s7 2 7 7z" fill="#ffc23a"/></svg></span><span class="seat"><svg width="16" height="16" viewBox="0 0 16 16"><circle cx="8" cy="5" r="4" fill="#ffc23a"/><path d="M1 16c0-5 3-7 7-7s7 2 7 7z" fill="#ffc23a"/></svg></span><span class="seat"><svg width="16" height="14" viewBox="0 0 16 14"><path d="M4 0h8v6h4l-8 8-8-8h4z" fill="#7a0a08"/></svg></span><span class="seat"><svg width="16" height="14" viewBox="0 0 16 14"><path d="M4 0h8v6h4l-8 8-8-8h4z" fill="#7a0a08"/></svg></span></div>
    </article>

    <article class="abs card" style="left:848px;top:458px">
      <span class="card-title">Baccarat A5-3C</span><span class="card-comm">Commission 0/7</span>
      <span class="card-limit">Bet Limit</span><span class="card-count">0/100</span>
      <span class="join">JOIN</span>
      <svg class="board" width="310" height="54" viewBox="0 0 310 54"><g fill="none" stroke="#fff" stroke-width="1"><polygon points="22,2 288,2 304,52 6,52"/><line x1="19" y1="12" x2="291" y2="12"/><line x1="13" y1="30" x2="297" y2="30"/><line x1="60" y1="2" x2="48.6" y2="52"/><line x1="98" y1="2" x2="91.1" y2="52"/><line x1="136" y1="2" x2="133.7" y2="52"/><line x1="174" y1="2" x2="176.3" y2="52"/><line x1="212" y1="2" x2="218.9" y2="52"/><line x1="250" y1="2" x2="261.4" y2="52"/></g><g fill="#fff" font-family="Open Sans, sans-serif" font-style="italic" font-weight="700" font-size="12" text-anchor="middle"><text x="35" y="26">B</text><text x="75" y="26">B</text><text x="115" y="26">B</text><text x="155" y="26">B</text><text x="195" y="26">B</text><text x="235" y="26">B</text><text x="275" y="26">B</text><text x="30" y="46">P</text><text x="72" y="46">P</text><text x="114" y="46">P</text><text x="155" y="46">P</text><text x="197" y="46">P</text><text x="239" y="46">P</text><text x="280" y="46">P</text></g></svg>
      <div class="seats"><span class="seat"><svg width="16" height="16" viewBox="0 0 16 16"><circle cx="8" cy="5" r="4" fill="#ffc23a"/><path d="M1 16c0-5 3-7 7-7s7 2 7 7z" fill="#ffc23a"/></svg></span><span class="seat"><svg width="16" height="16" viewBox="0 0 16 16"><circle cx="8" cy="5" r="4" fill="#ffc23a"/><path d="M1 16c0-5 3-7 7-7s7 2 7 7z" fill="#ffc23a"/></svg></span><span class="seat"><svg width="16" height="16" viewBox="0 0 16 16"><circle cx="8" cy="5" r="4" fill="#ffc23a"/><path d="M1 16c0-5 3-7 7-7s7 2 7 7z" fill="#ffc23a"/></svg></span><span class="seat"><svg width="16" height="16" viewBox="0 0 16 16"><circle cx="8" cy="5" r="4" fill="#ffc23a"/><path d="M1 16c0-5 3-7 7-7s7 2 7 7z" fill="#ffc23a"/></svg></span><span class="seat"><svg width="16" height="16" viewBox="0 0 16 16"><circle cx="8" cy="5" r="4" fill="#ffc23a"/><path d="M1 16c0-5 3-7 7-7s7 2 7 7z" fill="#ffc23a"/></svg></span><span class="seat"><svg width="16" height="14" viewBox="0 0 16 14"><path d="M4 0h8v6h4l-8 8-8-8h4z" fill="#7a0a08"/></svg></span><span class="seat"><svg width="16" height="14" viewBox="0 0 16 14"><path d="M4 0h8v6h4l-8 8-8-8h4z" fill="#7a0a08"/></svg></span></div>
    </article>
  </section>

  <div class="abs scroll"></div>
  <div class="abs thumb"></div>

  <footer class="abs footer"></footer>
  <div class="abs balance">Balance<span class="currency">$SGD</span><span class="amount">999,999.999</span></div>
</main>
</body>
</html>
```